Business Card Design for ReaL ESTATE AGENT

New Business Cards for a real estate agent in Jacksonville, FL. My specialty is urban core, historic districts but sell through out the city. Company Name is Ninth and Crest Realty a division of the Dunholt Companies. The card needs to convey an essence of professionalism, knowledge and success.

Target Market(s)

Home buyers and Sellers

Industry/Entity Type

Real Estate

Contact Information for Business Card

Double sided

Font styles to use
Sans Serif

Requirements
Must have
• My logs and photo (provided). My contact information as follows:
• Owen Talbrick
• Cell 904-555-0183
• Office 904-555-0147
• Email owentalbrick@mailbrook.example
Nice to have
• Tag Line - Exceptional Effort. Proven Results.

```html
<!DOCTYPE html>
<html lang="en">
<head>
<meta charset="utf-8">
<title>Ninth and Crest Realty – Business Card</title>
<link href="https://fonts.googleapis.com/css2?family=Open+Sans:wght@400;600;700&display=swap" rel="stylesheet">
<style>
  :root {
    --backdrop: #ece8e2;
    --card-white: #ffffff;
    --card-shade: #ededed;
    --brand-green: #22654f;
    --brand-red: #e0533b;
    --ink-light: #ffffff;
    --photo-dark: #3b3f45;
    --photo-light: #d9d6d2;
  }
  * { margin: 0; padding: 0; box-sizing: border-box; }
  html, body {
    width: 1200px; height: 900px; overflow: hidden;
    background: var(--backdrop);
    font-family: "Open Sans", Arial, sans-serif;
  }
  .canvas { position: relative; width: 1200px; height: 900px; }

  .card {
    position: absolute;
    width: 560px; height: 320px;
    background: var(--card-white);
    box-shadow: 0 8px 24px rgba(0,0,0,0.18);
    overflow: hidden;
  }

  /* Front side */
  .card--front { left: 130px; top: 120px; }
  .front-brand {
    position: absolute; inset: 0;
    display: flex; align-items: center; justify-content: center; gap: 18px;
  }
  .brand-mark {
    width: 54px; height: 54px;
    border: 5px solid var(--brand-green);
  }
  .brand-name {
    color: var(--brand-green);
    font-weight: 700; font-size: 34px; line-height: 1.1;
    text-transform: uppercase; letter-spacing: 1px;
  }

  /* Back side */
  .card--back {
    left: 510px; top: 460px;
    background: linear-gradient(180deg, var(--card-shade) 0%, var(--card-white) 45%);
  }
  .agent-photo {
    position: absolute; left: 52px; top: 26px;
    width: 240px; height: 174px;
    background: linear-gradient(180deg, var(--photo-light) 0%, #b9b3ad 45%, var(--photo-dark) 100%);
  }
  .back-brand {
    position: absolute; right: 28px; top: 48px;
    display: flex; align-items: center; gap: 10px;
  }
  .back-brand .brand-mark { width: 34px; height: 34px; border-width: 4px; }
  .back-brand .brand-name { font-size: 18px; letter-spacing: 0.5px; }

  .info-band {
    position: absolute; left: 0; right: 0; bottom: 0; height: 120px;
    background: var(--brand-green);
    color: var(--ink-light);
  }
  .agent {
    position: absolute; left: 150px; top: 24px; text-align: right; width: 240px; left: 60px;
  }
  .agent-name { font-size: 26px; font-weight: 400; line-height: 1.1; }
  .agent-title { font-size: 15px; font-weight: 400; }

  .contact-list {
    position: absolute; left: 340px; top: -6px;
    list-style: none;
  }
  .card--back .contact-list { top: 212px; left: 360px; position: absolute; }
  .contact-item {
    display: flex; align-items: center; gap: 8px;
    font-size: 13px; color: var(--ink-light); margin-bottom: 6px;
  }
  .contact-icon {
    width: 16px; height: 16px; background: var(--ink-light); border-radius: 3px;
    display: flex; align-items: center; justify-content: center;
  }
</style>
</head>
<body>
<main class="canvas">

  <section class="card card--front" aria-label="Card front">
    <div class="front-brand">
      <span class="brand-mark"></span>
      <span class="brand-name">Ninth and Crest<br>Realty</span>
    </div>
  </section>

  <section class="card card--back" aria-label="Card back">
    <div class="agent-photo" role="img" aria-label="Portrait photo of the agent in a dark suit"></div>
    <div class="back-brand">
      <span class="brand-mark"></span>
      <span class="brand-name">Ninth and Crest<br>Realty</span>
    </div>

    <div class="info-band">
      <div class="agent">
        <p class="agent-name">Halden Merrow</p>
        <p class="agent-title">Managing Director</p>
      </div>
    </div>

    <ul class="contact-list">
      <li class="contact-item">
        <span class="contact-icon">
          <svg width="12" height="12" viewBox="0 0 24 24" aria-hidden="true"><path fill="#22654f" d="M6.6 10.8a15 15 0 0 0 6.6 6.6l2.2-2.2c.3-.3.7-.4 1-.2 1.1.4 2.3.6 3.6.6.6 0 1 .4 1 1V20c0 .6-.4 1-1 1C10.6 21 3 13.4 3 4c0-.6.4-1 1-1h3.5c.6 0 1 .4 1 1 0 1.3.2 2.5.6 3.6.1.3 0 .7-.2 1z"/></svg>
        </span>
        (044)-555-0126
      </li>
      <li class="contact-item">
        <span class="contact-icon">
          <svg width="12" height="12" viewBox="0 0 24 24" aria-hidden="true"><rect x="2" y="5" width="20" height="14" rx="1" fill="#22654f"/><path d="M2 6l10 7 10-7" stroke="#fff" stroke-width="2" fill="none"/></svg>
        </span>
        info@merrowmail.example
      </li>
    </ul>
  </section>

</main>
</body>
</html>
```